Create a wordpress website for Tovarin business solution

This project is to create a complete website with all pages.

Overview
The purpose of this project is to create a full complete website with all pages (16 pages). The site should be professional and modern. The site is for an IT recruiting and IT training company. The site needs to be easy to administer and update content. It should be simple to add pages, videos and testimonials later. I will leave the site layout, color schemes and flow to the designers.

Navigation Menu (Home, who we are, what we do, what makes us different, why it matters, candidate portal, contact us, Blog)

WHO WE ARE should be a drop down menu with link to pages (about us, mission, vision and purpose, our team)

WHAT WE DO should be drop down menu with link to the following pages (IT Recruiting, IT Training, Hardware and software sales)

What makes us different should be single page with different paragraph titles. (We live what we do, we don't compromise quality, we share knowledge, staffing guarantee)

Why it matters should be single page with paragraph titles. (Quickly fill positions, candidate career development)

Candidate portal should links to my portal login page. I can add the correct URL later. I just need it to link to somewhere. I can change it.

Contact us should have (address, phone number, google map and a form to submit request for a call back)

Blog - This link should launch a wordpress blogging module

Target Market(s)

IT RECRUITING AND CONSULTING

Industry/Entity Type

It Company

Coding

Coded - Design and coding required

Requirements
Must have
• Company Logo
• Navigation Menu (Home, who we are, what we do, what makes us different, why it matters, candidate portal, contact us)
• WHO WE ARE should be a drop down menu with link to pages (about us, mission, vision and purpose, our team)
• WHAT WE DO should be drop down menu with link to the following pages (IT Recruiting, IT Training, Hardware and software sales)
• What makes us different should be single page with different paragraph titles. (We live what we do, we don't compromise quality, we share knowledge, staffing guarantee)
• Why it matters should be single page with paragraph titles. (Quickly fill positions, candidate career development)
• Candidate portal should links to my portal login page. I can add the correct URL later. I just need it to link to somewhere. I can change it.
• Contact us should have (address, phone number, google map and a form to submit request for a call back)

```html
<!DOCTYPE html>
<html lang="en">
<head>
<meta charset="utf-8">
<title>Tovarin Business Solution</title>
<link rel="stylesheet" href="https://fonts.googleapis.com/css2?family=Questrial&family=Montserrat:wght@400;600;700&family=Open+Sans:wght@400;600&display=swap">
<style>
:root{
  --blue:#0b55a0;
  --blue-dark:#073f7a;
  --blue-mid:#1f6db5;
  --btn-blue:#1e73be;
  --orange:#e57a1e;
  --ink:#2b2b2b;
  --muted:#8a8a8a;
  --line:#e3e3e3;
  --white:#ffffff;
}
*{box-sizing:border-box;margin:0;padding:0}
html,body{width:1200px;height:3158px;overflow:hidden}
body{font-family:"Questrial",sans-serif;color:var(--ink);background:var(--white);position:relative}
.abs{position:absolute}

/* header */
.site-header{position:absolute;left:0;top:0;width:1200px;height:118px;background:var(--white)}
.brand{left:99px;top:30px;display:flex;align-items:center;gap:14px}
.brand-mark{width:26px;height:26px;border-radius:50%;background:var(--orange)}
.brand-name{font-family:"Questrial",sans-serif;font-size:36px;color:var(--blue);letter-spacing:.5px}
.auth{top:48px;height:34px;width:127px;font-size:14px;display:flex;align-items:center;justify-content:center;text-transform:uppercase}
.auth-login{left:827px;background:var(--orange);color:var(--white)}
.auth-signup{left:972px;border:1.5px solid var(--blue);color:var(--blue)}

.main-nav{position:absolute;left:0;top:118px;width:1200px;height:52px;background:var(--blue);display:flex;align-items:center;padding-left:99px;gap:30px}
.main-nav span{color:var(--white);font-family:"Open Sans",sans-serif;font-size:14px;text-transform:uppercase}
.caret{font-size:10px;margin-left:4px}

/* hero */
.hero{position:absolute;left:0;top:170px;width:1200px;height:533px;
  background:linear-gradient(100deg,#24405e 0%,#3d5a78 40%,#6d7f92 65%,#2a3a4f 100%)}
.hero-title{left:99px;top:128px;font-family:"Montserrat",sans-serif;font-weight:700;font-size:43px;line-height:54px;color:var(--white);text-transform:uppercase}
.hero-sub{left:99px;top:248px;font-size:22px;color:var(--white)}
.hero-btn{left:99px;top:302px;width:193px;height:52px;background:var(--orange);color:var(--white);font-family:"Montserrat",sans-serif;font-weight:600;font-size:18px;display:flex;align-items:center;justify-content:center}
.hero-arrows{left:99px;top:390px;display:flex;gap:8px}
.hero-arrows span{width:32px;height:32px;border-radius:50%;background:#1c1c1c;display:flex;align-items:center;justify-content:center}

/* welcome */
.welcome{position:absolute;left:0;top:703px;width:1200px;height:555px;background:var(--white)}
.section-title{position:absolute;left:0;width:1200px;text-align:center;font-size:32px;text-transform:uppercase;color:var(--ink)}
.section-title em{font-style:normal;color:var(--blue)}
.intro{position:absolute;left:200px;width:800px;text-align:center;font-family:"Open Sans",sans-serif;font-size:13px;line-height:27px;color:var(--muted)}
.service-card{top:244px;width:307px;height:244px;border:1px solid var(--line);text-align:center}
.service-icon{position:absolute;left:50%;top:-63px;margin-left:-59px;width:118px;height:118px;border-radius:50%;background:var(--blue);border:7px solid #eef3f8;display:flex;align-items:center;justify-content:center}
.service-name{position:absolute;top:80px;left:0;width:100%;font-size:20px;text-transform:uppercase}
.service-text{position:absolute;top:120px;left:26px;right:26px;font-family:"Open Sans",sans-serif;font-size:11.5px;line-height:21px;color:var(--muted)}
.service-more{position:absolute;top:198px;left:0;width:100%;font-family:"Montserrat",sans-serif;font-weight:700;font-size:12px;color:var(--blue)}

/* about */
.about{position:absolute;left:0;top:1258px;width:1200px;height:407px;
  background:linear-gradient(110deg,#1a5fa6 0%,#2e76bb 50%,#1b5b9c 100%)}
.about .section-title{color:var(--white);font-size:50px;top:52px}
.about-text{position:absolute;left:130px;width:940px;text-align:center;font-family:"Open Sans",sans-serif;font-size:15px;line-height:34px;color:var(--white)}
.ghost-btn{left:488px;top:283px;width:224px;height:48px;border:1.5px solid var(--white);color:var(--white);font-size:22px;display:flex;align-items:center;justify-content:center}

/* blog */
.blog{position:absolute;left:0;top:1665px;width:1200px;height:583px;background:var(--white)}
.post{top:122px;width:315px}
.post-image{width:315px;height:183px}
.post-title{margin-top:34px;font-family:"Montserrat",sans-serif;font-weight:700;font-size:17px;line-height:22px;text-transform:uppercase;color:#1b1b1b}
.post-text{margin-top:16px;font-family:"Open Sans",sans-serif;font-size:13.5px;line-height:22px;color:#666}
.post-btn{margin-top:26px;width:124px;height:38px;background:var(--btn-blue);color:var(--white);font-family:"Montserrat",sans-serif;font-weight:600;font-size:13px;display:flex;align-items:center;justify-content:center;gap:8px}

/* testimonials */
.testimonials{position:absolute;left:0;top:2248px;width:1200px;height:303px;
  background:linear-gradient(180deg,#1a5a9e 0%,#2a6aa9 70%,#3c7ab4 100%)}
.testimonials .section-title{color:var(--white);top:44px;font-size:31px}
.quote-badge{left:99px;top:108px;width:112px;height:112px;border-radius:50%;background:#e8e8e8;display:flex;align-items:center;justify-content:center}
.avatar{left:175px;top:104px;width:112px;height:112px;border-radius:50%;background:linear-gradient(160deg,#d9d9d9,#9aa0a6);border:5px solid var(--white)}
.quote-text{left:310px;top:116px;width:790px;font-family:"Open Sans",sans-serif;font-style:italic;font-size:12.5px;line-height:20px;color:var(--white)}
.quote-name{left:310px;top:196px;font-family:"Montserrat",sans-serif;font-weight:700;font-size:12px;color:var(--white)}
.dots{left:0;top:256px;width:1200px;display:flex;justify-content:center;gap:8px}
.dots span{width:9px;height:9px;border-radius:50%;border:1.5px solid var(--white)}
.dots .on{background:var(--white)}

/* contact */
.contact{position:absolute;left:0;top:2551px;width:1200px;height:527px;background:#f7f9fc}
.contact .section-title{top:44px}
.contact-sub{position:absolute;top:106px;left:0;width:1200px;text-align:center;font-family:"Open Sans",sans-serif;font-size:15px;color:#444}
.field{background:var(--white);border:1px solid #dcdcdc;font-family:"Open Sans",sans-serif;font-size:12px;color:#999;padding:10px 14px}
.send-btn{left:99px;top:417px;width:210px;height:46px;background:var(--orange);color:var(--white);font-size:19px;text-transform:uppercase;display:flex;align-items:center;justify-content:center}
.info-label{font-family:"Open Sans",sans-serif;font-size:18px;color:#333}
.info-line{font-family:"Open Sans",sans-serif;font-size:13.5px;line-height:21px;color:#666;display:flex;gap:10px}
.info-line svg{flex:none;margin-top:4px}

/* footer */
.site-footer{position:absolute;left:0;top:3078px;width:1200px;height:80px;background:var(--blue);color:var(--white);font-family:"Open Sans",sans-serif;font-size:14px}
.social{left:880px;top:22px;display:flex;gap:8px}
.social span{width:38px;height:38px;border-radius:50%;border:2px solid var(--white);background:var(--blue-mid)}
</style>
</head>
<body>

<header class="site-header">
  <div class="abs brand"><span class="brand-mark"></span><span class="brand-name">Tovarin Business Solution LLC</span></div>
  <div class="abs auth auth-login">Login</div>
  <div class="abs auth auth-signup">Sign up</div>
</header>

<nav class="main-nav">
  <span>Home</span>
  <span>Who we are<span class="caret">&#9662;</span></span>
  <span>What we do<span class="caret">&#9662;</span></span>
  <span>What makes us different</span>
  <span>Why it matters</span>
  <span>Candidate portal</span>
  <span>Blog</span>
  <span>Contact us</span>
</nav>

<section class="hero" role="img" aria-label="Businessman touching a network of people icons">
  <h1 class="abs hero-title">Tovarin Business<br>Solution</h1>
  <p class="abs hero-sub">We are IT recruiting and IT training company</p>
  <div class="abs hero-btn">LEARN MORE &raquo;</div>
  <div class="abs hero-arrows">
    <span><svg width="12" height="12" viewBox="0 0 12 12"><path d="M8 1L3 6l5 5" fill="none" stroke="#fff" stroke-width="2"/></svg></span>
    <span><svg width="12" height="12" viewBox="0 0 12 12"><path d="M4 1l5 5-5 5" fill="none" stroke="#fff" stroke-width="2"/></svg></span>
  </div>
</section>

<section class="welcome">
  <h2 class="section-title" style="top:52px">Welcome to <em>Tovarin Business Solution</em></h2>
  <p class="intro" style="top:102px">Sed ut perspiciatis unde omnis iste natus error sit voluptatem accusantium doloremque laudantium, totam rem aperiam, eaque ipsa quae ab illo inventore veritatis et quasi architecto beatae vitae dicta sunt explicabo</p>

  <div class="abs service-card" style="left:99px">
    <div class="service-icon"><svg width="54" height="40" viewBox="0 0 54 40" fill="#fff"><circle cx="27" cy="9" r="7"/><path d="M15 34c0-9 5-14 12-14s12 5 12 14z"/><circle cx="11" cy="13" r="5"/><path d="M2 34c0-7 4-11 9-11 2 0 3 1 4 2-2 3-3 6-3 9z"/><circle cx="43" cy="13" r="5"/><path d="M52 34c0-7-4-11-9-11-2 0-3 1-4 2 2 3 3 6 3 9z"/></svg></div>
    <h3 class="service-name">IT Recruiting</h3>
    <p class="service-text">Quis autem vel eum iure reprehenderit qui in ea voluptate velit esse quam nihil molestiae consequatur vel illum qui dolorem.</p>
    <div class="service-more">READ MORE &#10148;</div>
  </div>
  <div class="abs service-card" style="left:444px">
    <div class="service-icon"><svg width="50" height="46" viewBox="0 0 50 46" fill="none" stroke="#fff" stroke-width="2.5"><rect x="8" y="3" width="38" height="26"/><path d="M16 44l8-15 8 15" /><circle cx="10" cy="24" r="4" fill="#fff"/><path d="M4 44v-10h12v10" fill="#fff"/><path d="M22 22l8-8 5 5 6-8"/></svg></div>
    <h3 class="service-name">IT Training</h3>
    <p class="service-text">Quis autem vel eum iure reprehenderit qui in ea voluptate velit esse quam nihil molestiae consequatur vel illum qui dolorem.</p>
    <div class="service-more">READ MORE &#10148;</div>
  </div>
  <div class="abs service-card" style="left:792px">
    <div class="service-icon"><svg width="58" height="36" viewBox="0 0 58 36" fill="#fff"><path d="M2 8l10-4 8 4-10 16-8-6z"/><path d="M56 8l-10-4-10 3-10 8 4 3 8-5 12 12 6-5z"/><path d="M14 24l6 5 4 4 4 1 4-2 4 1 4-4-10-10-8 5z"/></svg></div>
    <h3 class="service-name">Business Solution</h3>
    <p class="service-text">Quis autem vel eum iure reprehenderit qui in ea voluptate velit esse quam nihil molestiae consequatur vel illum qui dolorem.</p>
    <div class="service-more">READ MORE &#10148;</div>
  </div>
</section>

<section class="about" role="img" aria-label="Blue-tinted photo of hands typing on a laptop">
  <h2 class="section-title">About us</h2>
  <p class="about-text" style="top:118px">But I must explain to you how all this mistaken idea of denouncing pleasure and praising pain was born and I will give you a complete account of the system, and expound the actual teachings of the great explorer of the truth</p>
  <p class="about-text" style="top:188px">Quis autem vel eum iure reprehenderit qui in ea voluptate velit esse quam nihil molestiae consequatur, vel illum qui dolorem eum fugiat quo voluptas nulla pariatur</p>
  <div class="abs ghost-btn">READ MORE</div>
</section>

<section class="blog">
  <h2 class="section-title" style="top:42px;font-size:30px">Latest blog</h2>
  <article class="abs post" style="left:99px">
    <div class="post-image" role="img" aria-label="Team of smiling colleagues at a meeting table" style="background:linear-gradient(120deg,#d8d2c8,#8a8f99 60%,#3a3f4a)"></div>
    <h3 class="post-title">Beatae vitae dicta sunt explicabo</h3>
    <p class="post-text">Excepteur sint occaecat cupidatat non proident, sunt in culpa qui officia deserunt mollit anim id est laborum...</p>
    <div class="post-btn">Read More <span>&#8250;</span></div>
  </article>
  <article class="abs post" style="left:442px">
    <div class="post-image" role="img" aria-label="Business people reviewing documents at a desk" style="background:linear-gradient(120deg,#e9edf2,#5d6b80 55%,#1d2636)"></div>
    <h3 class="post-title">Reprehenderit qui in ea voluptate velit</h3>
    <p class="post-text">Excepteur sint occaecat cupidatat non proident, sunt in culpa qui officia deserunt mollit anim id est laborum...</p>
    <div class="post-btn">Read More <span>&#8250;</span></div>
  </article>
  <article class="abs post" style="left:785px">
    <div class="post-image" role="img" aria-label="Handshake over a wooden desk" style="background:linear-gradient(120deg,#2a2a2a,#6b5a48 50%,#c9b79d)"></div>
    <h3 class="post-title">Vel illum qui dolorem eum fugiat quo</h3>
    <p class="post-text">Excepteur sint occaecat cupidatat non proident, sunt in culpa qui officia deserunt mollit anim id est laborum...</p>
    <div class="post-btn">Read More <span>&#8250;</span></div>
  </article>
</section>

<section class="testimonials" role="img" aria-label="Blue-tinted office background">
  <h2 class="section-title">Client testimonials</h2>
  <div class="abs quote-badge"><svg width="40" height="30" viewBox="0 0 40 30" fill="#c4c4c4"><path d="M0 30V16C0 6 6 1 14 0v6c-4 1-7 4-7 8h7v16zM22 30V16c0-10 6-15 14-16v6c-4 1-7 4-7 8h7v16z"/></svg></div>
  <div class="abs avatar" role="img" aria-label="Client portrait"></div>
  <p class="abs quote-text">At vero eos et accusamus et iusto odio dignissimos ducimus qui blanditiis praesentium voluptatum deleniti atque corrupti quos dolores et quas molestias excepturi sint occaecati cupiditate non provident, similique sunt in culpa qui officia deserunt mollitia animi, id est laborum et dolorum fuga. Et harum quidem rerum facilis est et expedita distinctio.</p>
  <div class="abs quote-name">- MARCUS DALE</div>
  <div class="abs dots"><span></span><span class="on"></span><span></span><span></span></div>
</section>

<section class="contact">
  <h2 class="section-title">Contact us</h2>
  <p class="contact-sub">Contact us at the following for and general enquiries</p>

  <div class="abs field" style="left:99px;top:169px;width:286px;height:38px">Name *</div>
  <div class="abs field" style="left:402px;top:169px;width:284px;height:38px">Email *</div>
  <div class="abs field" style="left:99px;top:219px;width:587px;height:38px">Subject</div>
  <div class="abs field" style="left:99px;top:272px;width:587px;height:124px">Message *</div>
  <div class="abs send-btn">Send message</div>

  <div class="abs" style="left:836px;top:166px">
    <div class="info-label">Email</div>
    <div class="info-line" style="margin-top:4px"><svg width="14" height="11" viewBox="0 0 14 11"><rect width="14" height="11" fill="var(--orange)"/><path d="M0 0l7 6 7-6" fill="none" stroke="#fff" stroke-width="1.3"/></svg>Contact@domainname.com</div>
    <div class="info-label" style="margin-top:30px">Phone</div>
    <div class="info-line" style="margin-top:4px"><svg width="14" height="11" viewBox="0 0 14 11"><rect width="14" height="11" fill="var(--orange)"/><path d="M0 0l7 6 7-6" fill="none" stroke="#fff" stroke-width="1.3"/></svg>+11 1234 56789</div>
    <div class="info-label" style="margin-top:30px">Address</div>
    <div class="info-line" style="margin-top:4px"><svg width="12" height="14" viewBox="0 0 12 14"><path d="M6 0L0 6h2v8h3V10h2v4h3V6h2z" fill="var(--orange)"/></svg><span>Tovarin Business Solution<br>148 Street Address<br>City Address, State<br>Country.</span></div>
  </div>
</section>

<footer class="site-footer">
  <div class="abs" style="left:99px;top:30px">&copy; 2016 Tovarin Business Solution . All right reserved.&nbsp;&nbsp; Term of Use</div>
  <div class="abs" style="left:772px;top:30px">Connect With Us:</div>
  <div class="abs social"><span></span><span></span><span></span><span></span></div>
</footer>

</body>
</html>
```